Photography Business, Business Card

Looking for a unique cutting edge card that takes advantage of the latest printing technologies. Please review this site for all the options they office: https://glowprintly.com. If you can think it they can do it. And if you have an idea and do not know if they can do it, I will check into it.

Target Market(s)

People and places I took images of and future clients.

Industry/Entity Type

Photography

Contact Information for Business Card

Name, cell & email. Derek Holloway, dholloway@kpnvisuals.com, 312-748-2961

Colors

Designer to choose only greyscale colors for use in the design.

Requirements
Must have
• 100% cutting edge. Is so great, those I hand it to always show it to someone else. A piece of art.
Nice to have
• Blacks, silvers, greys, some red. Maybe other colors?

```html
<!DOCTYPE html>
<html lang="en">
<head>
<meta charset="utf-8">
<title>Derek Holloway Photography – Business Card</title>
<link rel="stylesheet" href="https://fonts.googleapis.com/css2?family=Open+Sans:wght@400;600;700&display=swap">
<style>
  :root {
    --page-bg: #2b2b2d;
    --card-black: #141414;
    --card-edge: #2a2a2a;
    --silver-light: #e6e6e6;
    --silver-mid: #9a9a9a;
    --silver-dark: #4a4a4a;
    --text-grey: #b4b4b4;
    --text-soft: #9c9c9c;
    --accent-red: #e3232b;
  }
  * { box-sizing: border-box; margin: 0; padding: 0; }
  html, body { width: 1200px; height: 875px; overflow: hidden; }
  body {
    background: var(--page-bg);
    font-family: "Open Sans", Arial, sans-serif;
    position: relative;
  }
  .card {
    position: absolute;
    left: 290px;
    width: 620px;
    height: 368px;
  }
  .card--front { top: 48px; }
  .card--back { top: 460px; }
  .card__shape { position: absolute; inset: 0; width: 620px; height: 368px; }

  /* Front side */
  .signature {
    position: absolute;
    left: 130px;
    top: 110px;
    width: 250px;
    height: 170px;
    border-radius: 60px 20px 70px 20px;
    background: linear-gradient(120deg, var(--silver-dark), var(--silver-light) 45%, var(--silver-mid) 70%, var(--silver-dark));
    opacity: 0.55;
  }
  .front-tagline {
    position: absolute;
    left: 396px;
    top: 176px;
    font-size: 17px;
    letter-spacing: 5px;
    color: var(--text-soft);
    font-weight: 400;
    white-space: nowrap;
  }

  /* Back side */
  .brand-name {
    position: absolute;
    left: 46px;
    top: 92px;
    font-size: 62px;
    font-weight: 700;
    letter-spacing: 4px;
    color: var(--accent-red);
    line-height: 1;
  }
  .person-name {
    position: absolute;
    left: 48px;
    top: 178px;
    font-size: 30px;
    font-weight: 700;
    color: var(--text-grey);
    line-height: 1;
  }
  .person-role {
    position: absolute;
    left: 50px;
    top: 214px;
    font-size: 17px;
    font-weight: 600;
    color: var(--accent-red);
  }
  .contact-list {
    position: absolute;
    left: 50px;
    top: 254px;
    list-style: none;
  }
  .contact-list li {
    display: flex;
    align-items: center;
    gap: 10px;
    font-size: 15px;
    color: var(--text-soft);
    line-height: 24px;
  }
  .contact-icon { width: 13px; height: 13px; flex: none; }
  .shutter-mark {
    position: absolute;
    left: 372px;
    top: 70px;
    width: 220px;
    height: 220px;
    border-radius: 50%;
    background: radial-gradient(circle at 35% 30%, var(--silver-light), var(--silver-mid) 45%, #2e2e2e 80%);
  }
</style>
</head>
<body>

<section class="card card--front" aria-label="Card front">
  <svg class="card__shape" viewBox="0 0 620 368">
    <path d="M22 28 H150 V12 H170 V0 H300 V12 H320 V28 H598 Q620 28 620 50 V346 Q620 368 598 368 H22 Q0 368 0 346 V50 Q0 28 22 28 Z" fill="var(--card-black)" stroke="var(--card-edge)" stroke-width="1.5"/>
  </svg>
  <div class="signature" role="img" aria-label="Silver foil handwritten signature of Derek Holloway"></div>
  <p class="front-tagline">PHOTOGRAPHY</p>
</section>

<section class="card card--back" aria-label="Card back">
  <svg class="card__shape" viewBox="0 0 620 368">
    <path d="M22 28 H80 V12 H100 V0 H230 V12 H250 V28 H598 Q620 28 620 50 V346 Q620 368 598 368 H22 Q0 368 0 346 V50 Q0 28 22 28 Z" fill="var(--card-black)" stroke="var(--card-edge)" stroke-width="1.5"/>
  </svg>
  <p class="brand-name">HLWY</p>
  <h1 class="person-name">Derek Holloway</h1>
  <p class="person-role">Photography</p>
  <ul class="contact-list">
    <li>
      <svg class="contact-icon" viewBox="0 0 13 13"><rect x="3" y="0.5" width="7" height="12" rx="1.5" fill="none" stroke="var(--accent-red)" stroke-width="1.5"/><circle cx="6.5" cy="10" r="0.9" fill="var(--accent-red)"/></svg>
      312-748-2961
    </li>
    <li>
      <svg class="contact-icon" viewBox="0 0 13 13"><rect x="0.5" y="2.5" width="12" height="8" fill="var(--accent-red)"/><path d="M0.5 2.5 L6.5 7 L12.5 2.5" fill="none" stroke="var(--card-black)" stroke-width="1.2"/></svg>
      dholloway@kpnvisuals.com
    </li>
    <li>
      <svg class="contact-icon" viewBox="0 0 13 13"><circle cx="6.5" cy="6.5" r="5.5" fill="none" stroke="var(--accent-red)" stroke-width="1.5"/><path d="M1 6.5 H12 M6.5 1 C3.5 4 3.5 9 6.5 12 M6.5 1 C9.5 4 9.5 9 6.5 12" fill="none" stroke="var(--accent-red)" stroke-width="1"/></svg>
      www.hlwyvisuals.com
    </li>
  </ul>
  <div class="shutter-mark" role="img" aria-label="Large silver foil camera shutter emblem"></div>
</section>

</body>
</html>
```